Recipe Card Design

I have a small kitchen store in Livingston Montana, and I would like to have recipe cards (4x6 postcard) designed with my logo, lines for recipe writing, all in black and white. My website is here: www.brambleforkcookware.com

Store

```html
<!DOCTYPE html>
<html lang="en">
<head>
<meta charset="utf-8">
<title>Bramble Fork Cookware Shop – Recipe Card</title>
<link rel="stylesheet" href="https://fonts.googleapis.com/css2?family=Oswald:wght@500;600;700&family=IM+Fell+English+SC&family=Amatic+SC:wght@400&family=Patrick+Hand&display=swap">
<style>
  :root {
    --backdrop: #e8e5e0;
    --paper: #ffffff;
    --ink: #1c1c1c;
    --ink-soft: #454545;
    --pattern-a: #f4f4f4;
    --pattern-b: #e9e9e9;
    --rule: #8a8a8a;
    --dots: #2a2a2a;
  }
  * { box-sizing: border-box; margin: 0; padding: 0; }
  html, body { width: 1200px; height: 1200px; overflow: hidden; }
  body { background: var(--backdrop); position: relative; color: var(--ink); }

  .card {
    position: absolute;
    width: 760px;
    height: 507px;
    background: var(--paper);
    box-shadow: 0 6px 18px rgba(0,0,0,0.18);
    overflow: hidden;
  }
  .card--front { left: 40px; top: 40px; }
  .card--back { left: 400px; top: 650px; }

  .icon-pattern {
    position: absolute; inset: 0;
    background: radial-gradient(circle at 30% 30%, var(--pattern-a), var(--paper) 55%),
                linear-gradient(135deg, var(--pattern-b), var(--paper));
    opacity: 0.9;
  }

  .shop-name {
    position: absolute;
    font-family: "Oswald", sans-serif;
    font-weight: 600;
    color: var(--ink-soft);
    text-align: center;
    text-transform: uppercase;
    line-height: 1.05;
  }
  .shop-name__mark {
    display: block; margin: 0 auto 14px;
    border: 4px solid var(--ink-soft);
  }
  .card--front .shop-name { left: 230px; top: 36px; width: 300px; }
  .card--front .shop-name__mark { width: 56px; height: 56px; }
  .card--front .shop-name__main { font-size: 52px; }
  .card--front .shop-name__sub { font-size: 30px; letter-spacing: 3px; margin-top: 6px; }
  .card--front .shop-name__place { font-size: 14px; letter-spacing: 5px; margin-top: 12px; }

  .section-title {
    position: absolute;
    font-family: "IM Fell English SC", serif;
    font-weight: 400;
    color: var(--ink);
  }
  .front__location-title { left: 0; width: 100%; top: 322px; text-align: center; font-size: 40px; }

  .front__address {
    position: absolute; left: 0; width: 100%; top: 386px; text-align: center;
    font-family: "Oswald", sans-serif; font-weight: 700; font-size: 22px; letter-spacing: 0.5px;
  }
  .front__contact {
    position: absolute; left: 0; width: 100%; top: 424px;
    display: flex; justify-content: center; align-items: center; gap: 10px;
    font-family: "Oswald", sans-serif; font-weight: 700; font-size: 22px;
  }
  .social-dot { width: 26px; height: 26px; border-radius: 6px; background: var(--ink); }
  .front__web {
    position: absolute; left: 0; width: 100%; top: 464px; text-align: center;
    font-family: "Oswald", sans-serif; font-weight: 700; font-size: 17px; text-transform: uppercase;
  }

  .card--back .shop-name { left: 20px; top: 24px; width: 200px; }
  .card--back .shop-name__mark { width: 34px; height: 34px; border-width: 3px; margin-bottom: 8px; }
  .card--back .shop-name__main { font-size: 34px; }
  .card--back .shop-name__sub { font-size: 20px; letter-spacing: 2px; margin-top: 4px; }
  .card--back .shop-name__place { font-size: 10px; letter-spacing: 3px; margin-top: 8px; }

  .back__recipe-word {
    position: absolute; left: 20px; top: 196px; width: 200px; text-align: center;
    font-family: "Amatic SC", sans-serif; font-size: 78px; line-height: 1; color: var(--ink-soft);
  }
  .back__banner { position: absolute; left: 18px; top: 284px; }

  .back__hours-title { left: 20px; top: 360px; width: 200px; text-align: center; font-size: 26px; }
  .back__hours {
    position: absolute; left: 32px; top: 394px;
    font-family: "Patrick Hand", cursive; font-size: 19px; line-height: 1.26; color: var(--ink);
  }

  .write-box {
    position: absolute;
    border: 4px dotted var(--dots);
    border-radius: 20px;
    padding: 46px 22px 14px;
  }
  .write-box--ingredients { left: 250px; top: 18px; width: 480px; height: 196px; }
  .write-box--instructions { left: 262px; top: 234px; width: 470px; height: 258px; }
  .write-box__title { top: 10px; left: 0; width: 100%; text-align: center; font-size: 28px; }
  .write-box__line { border-bottom: 1px dashed var(--rule); height: 21px; }
  .write-box--instructions .write-box__line { height: 18px; }

  .back__mitt {
    position: absolute; right: 8px; bottom: 8px; width: 38px; height: 44px;
    background: linear-gradient(160deg, #3a3a3a, #111);
    border-radius: 16px 16px 8px 8px;
  }
</style>
</head>
<body>

<section class="card card--front">
  <div class="icon-pattern" role="img" aria-label="Scattered light grey pattern of kitchen item icons"></div>

  <div class="shop-name">
    <span class="shop-name__mark"></span>
    <div class="shop-name__main">Bramble Fork</div>
    <div class="shop-name__sub">Cookware Shop</div>
    <div class="shop-name__place">Pinecrest, Colorado</div>
  </div>

  <h2 class="section-title front__location-title">Location</h2>
  <p class="front__address">218 North Elm Street, Pinecrest, CO 80452</p>
  <div class="front__contact">
    <span>(970) 555-0182</span>
    <span class="social-dot"></span>
    <span class="social-dot"></span>
    <span class="social-dot"></span>
  </div>
  <p class="front__web">www.brambleforkcookware.com</p>
</section>

<section class="card card--back">
  <div class="icon-pattern" role="img" aria-label="Scattered light grey pattern of kitchen item icons"></div>

  <div class="shop-name">
    <span class="shop-name__mark"></span>
    <div class="shop-name__main">Bramble Fork</div>
    <div class="shop-name__sub">Cookware Shop</div>
    <div class="shop-name__place">Pinecrest, Colorado</div>
  </div>

  <div class="back__recipe-word">Recepe</div>
  <svg class="back__banner" width="210" height="70" viewBox="0 0 210 70">
    <path d="M4 16 L206 4 L200 54 L10 66 Z" fill="#fff" stroke="#555" stroke-width="2"/>
  </svg>

  <h3 class="section-title back__hours-title">Hours</h3>
  <div class="back__hours">
    Tue.- Sat.:<br>9:30 am - 6:00 pm<br>Sun.:<br>11:00 am - 3:00 pm
  </div>

  <div class="write-box write-box--ingredients">
    <h3 class="section-title write-box__title">Ingredients</h3>
    <div class="write-box__line"></div>
    <div class="write-box__line"></div>
    <div class="write-box__line"></div>
    <div class="write-box__line"></div>
    <div class="write-box__line"></div>
    <div class="write-box__line"></div>
  </div>

  <div class="write-box write-box--instructions">
    <h3 class="section-title write-box__title">Instruction</h3>
    <div class="write-box__line"></div>
    <div class="write-box__line"></div>
    <div class="write-box__line"></div>
    <div class="write-box__line"></div>
    <div class="write-box__line"></div>
    <div class="write-box__line"></div>
    <div class="write-box__line"></div>
    <div class="write-box__line"></div>
    <div class="write-box__line"></div>
  </div>

  <div class="back__mitt" role="img" aria-label="Small engraved oven mitt illustration"></div>
</section>

</body>
</html>
```